CrestHornSupply.com

I need a new webdesign for a company in the San Jose/SF Bay area that showcases the financial benefits of buying used band instruments for junior high students.This would be opposed to the current and costly option of renting cheap quality instruments from the 2 or 3 local music stores that charge a monthly fee that over the years charges the buyer 3 or 4x over..
Instruments: focus in on Alto Sax, Trumpet, Flute, Clarinet, Trombone, Tenor Sax, Baritone
Target middle schools are Larkfield Middle School and Maple Middle School in San Jose, CA. Both have award winning band programs.
Files attached may or may not be important.
Tabs Needed and funtional
Contact
Shopping Cart
Select Instrument
Checkout
Add to Cart, etc.
Instuments
quantity, etc.
trade in your instrument/sell your instrument
ability to add or take away new instruments for sale. including pictures
Additional questions or info, feel free to ask
Updates
Hi Designers,
Project Deadline Extended
Reason: In the next week you will be receiving specific content that will be required to be had on the website.
New desigins are still welcome. Please continue to contact me if you have questions about your individual designs.
Thanks!
Crest Horn

```html
<!DOCTYPE html>
<html lang="en">
<head>
<meta charset="utf-8">
<title>Crest Horn Instruments</title>
<link href="https://fonts.googleapis.com/css2?family=Questrial&family=Open+Sans:wght@400;600;700&family=Roboto+Slab:wght@300;400&family=Josefin+Sans:wght@400&display=swap" rel="stylesheet">
<style>
:root{
  --red:#e3211a;
  --red-dark:#c3120c;
  --red-text:#d9231d;
  --green:#1f9a2a;
  --ink:#222;
  --grey-bg:#f6f6f6;
  --card-dark:#3d3d3d;
  --footer:#232323;
  --footer-text:#8a8a8a;
  --star:#f39a1e;
}
*{box-sizing:border-box;margin:0;padding:0}
html,body{width:914px;height:1200px;overflow:hidden;background:#fff}
body{position:relative;font-family:"Open Sans",sans-serif;color:var(--ink)}
.abs{position:absolute}

/* header */
.site-header{left:0;top:0;width:914px;height:84px;background:linear-gradient(#ee2a1f,var(--red-dark));border-bottom:2px solid var(--green)}
.brand{left:0;width:914px;top:22px;text-align:center;color:#fff;font-family:"Questrial",sans-serif;line-height:1}
.brand .l1{font-size:20px;display:block}
.brand .l2{font-size:21px;display:block;margin-top:3px}
.nav a{position:absolute;top:50px;color:#fff;font-family:"Questrial",sans-serif;font-size:13px;text-decoration:none;white-space:nowrap}
.account{top:18px;left:620px;color:#fff;font-size:9px;font-weight:600}
.cart-icon{left:705px;top:14px}
.currency{left:741px;top:15px;color:#fff;font-size:11px}

/* hero */
.hero-bg{left:0;top:84px;width:914px;height:291px;background:radial-gradient(ellipse at 4% 45%,rgba(40,160,50,.55),transparent 16%),radial-gradient(ellipse at 95% 40%,rgba(40,160,50,.55),transparent 16%),#fff}
.hero-photo{left:130px;top:84px;width:653px;height:269px;background:linear-gradient(100deg,#6a6a6a 0%,#3a3a3a 38%,#2c2c2c 45%,#4a4543 70%,#6b3b2c 88%,#3a3a3a 100%);box-shadow:0 10px 14px -8px rgba(0,0,0,.35)}
.hero-arrow{width:32px;height:32px;border-radius:50%;background:var(--green);border:2px solid #fff;top:201px}

/* welcome */
.welcome{left:0;top:375px;width:914px;height:190px;background:var(--grey-bg)}
.welcome h1{position:absolute;top:15px;width:914px;text-align:center;font-family:"Questrial",sans-serif;font-weight:400;font-size:20.5px;color:#555}
.welcome h1 span{color:var(--red-text)}
.feature-icon{width:75px;height:75px;border-radius:50%;background:var(--red);top:51px;display:flex;align-items:center;justify-content:center}
.welcome p{position:absolute;top:137px;width:914px;text-align:center;font-family:"Questrial",sans-serif;font-size:10.5px;line-height:14.5px;color:#666}

/* info cards */
.info-card{top:580px;width:203px;height:107px;background:linear-gradient(#7a7a7a,var(--card-dark));box-shadow:0 10px 10px -6px rgba(0,0,0,.3)}
.info-card .head{position:absolute;left:0;top:0;width:203px;height:40px;background:linear-gradient(90deg,#fff 0 24%,var(--red) 45%,#ec3b31)}
.info-card .badge{position:absolute;left:-2px;top:-12px;width:52px;height:52px;border-radius:50%;background:#fff}
.info-card .kicker{position:absolute;left:65px;top:8px;color:#fff;font-size:10px;font-weight:600}
.info-card .title{position:absolute;right:10px;top:20px;color:#fff;font-size:13px;font-weight:700}
.info-card .date{position:absolute;left:15px;top:45px;color:#fff;font-size:8.5px;font-style:italic}
.info-card .body{position:absolute;left:15px;top:58px;width:180px;color:#fff;font-size:8px;line-height:11px}
.info-card .go{position:absolute;right:-4px;bottom:-8px;width:24px;height:24px;border-radius:50%;background:#fff;display:flex;align-items:center;justify-content:center;box-shadow:0 1px 3px rgba(0,0,0,.3)}
.teachers{position:absolute;left:45px;top:40px;display:flex;gap:3px}
.teachers i{width:19px;height:15px;background:linear-gradient(#d9b49a,#8a6a55)}

/* featured */
.featured-bar{left:130px;top:713px;width:653px;height:32px;border:1px solid #ddd;background:linear-gradient(#fff,#f2f2f2)}
.featured-bar h2{position:absolute;left:13px;top:7px;font-size:13px;font-weight:700;color:#333}
.pager{top:4px;width:22px;height:22px;border:1px solid #bbb;background:#f4f4f4;display:flex;align-items:center;justify-content:center}
.product{top:756px;width:148px}
.product .shot{width:148px;height:129px;border:1px solid #ddd;background:radial-gradient(circle,#f0ead8,#fff 70%)}
.stars{margin:5px 0 0 2px;color:var(--star);font-size:12px;letter-spacing:1px}
.product h3{margin:0 0 0 2px;font-size:11.5px;font-weight:700;color:#e81a12}
.product p{margin:2px 0 0 4px;font-size:8px;line-height:11px;color:#222}
.price{margin:8px 0 0 4px;font-size:12px;font-weight:700}
.actions{display:flex;gap:4px;margin-top:8px}
.add{width:79px;height:19px;background:#2a2a2a;border-radius:2px;color:#fff;font-size:8px;font-weight:700;display:flex;align-items:center;gap:6px;padding-left:6px}
.mini{width:19px;height:19px;border:1px solid #bbb;display:flex;align-items:center;justify-content:center}

/* footer */
.site-footer{left:0;top:1011px;width:914px;height:189px;background:var(--footer)}
.footer-links{left:130px;top:1050px;font-family:"Roboto Slab",serif;font-weight:300;font-size:10px;color:var(--footer-text);display:flex}
.footer-links span{padding:0 8px;border-left:1px solid #444}
.footer-links span:first-child{padding-left:0;border:0}
.contact-line{top:1085px;display:flex;align-items:center;gap:6px;color:var(--footer-text);font-size:10px;white-space:nowrap}
.contact-line b{width:19px;height:19px;border-radius:50%;background:#777;display:flex;align-items:center;justify-content:center;flex:none}
.copyright{left:130px;top:1147px;font-size:7.5px;color:#777}
.copyright span{color:#ddd}
.news-title{left:562px;top:1047px;color:#ccc;font-family:"Josefin Sans",sans-serif;font-size:11px;letter-spacing:1.5px}
.news-title span{color:#fff;font-family:"Roboto Slab",serif;font-size:14px;letter-spacing:.5px}
.field{left:548px;width:228px;height:26px;background:#4a4a4a;color:#ddd;font-family:"Josefin Sans",sans-serif;font-size:11px;letter-spacing:2px;display:flex;align-items:center;justify-content:center}
.subscribe{background:#fff;color:#222;height:31px}
</style>
</head>
<body>

<header class="site-header abs"></header>
<div class="brand abs"><span class="l1">CREST HORN</span><span class="l2">INSTRUMENTS</span></div>
<nav class="nav">
  <a style="left:170px">Home</a><a style="left:237px">Courses</a><a style="left:316px">Facilities</a>
  <a style="left:576px">News</a><a style="left:638px">Events</a><a style="left:708px">Contact</a>
</nav>
<div class="account abs">Login &nbsp;|&nbsp; Register</div>
<svg class="cart-icon abs" width="26" height="20" viewBox="0 0 26 20"><path d="M1 3h4l3 10h11l3-7H7" fill="none" stroke="#fff" stroke-width="1.8"/><circle cx="10" cy="17" r="1.6" fill="#fff"/><circle cx="18" cy="17" r="1.6" fill="#fff"/><circle cx="20" cy="5" r="5" fill="#f22"/><text x="20" y="8" font-size="7" fill="#fff" text-anchor="middle" font-family="sans-serif">0</text></svg>
<div class="currency abs">$ &#8964;</div>

<div class="hero-bg abs" role="img" aria-label="Soft green smoke drifting on a white backdrop"></div>
<div class="hero-photo abs" role="img" aria-label="Photo of a trumpet player and a violinist performing"></div>
<div class="hero-arrow abs" style="left:93px"><svg width="28" height="28"><path d="M17 8l-6 6 6 6" fill="none" stroke="#fff" stroke-width="2.5"/></svg></div>
<div class="hero-arrow abs" style="left:792px"><svg width="28" height="28"><path d="M11 8l6 6-6 6" fill="none" stroke="#fff" stroke-width="2.5"/></svg></div>

<section class="welcome abs">
  <h1>WELCOME TO <span>CREST HORN INSTRUMENTS</span></h1>
  <div class="feature-icon abs" style="left:157px"><svg width="34" height="40"><rect x="11" y="3" width="12" height="20" rx="6" fill="#fff"/><path d="M7 17a10 10 0 0 0 20 0" fill="none" stroke="#fff" stroke-width="2"/><path d="M17 27v8M11 36h12" stroke="#fff" stroke-width="2"/></svg></div>
  <div class="feature-icon abs" style="left:290px"><svg width="34" height="40"><path d="M22 3l-4 6v18a5 5 0 0 1-10 0v-4" fill="none" stroke="#fff" stroke-width="4" stroke-linecap="round"/></svg></div>
  <div class="feature-icon abs" style="left:426px"><svg width="34" height="40"><path d="M18 38V4c5 3 5 9-3 15-6 4-5 12 2 12s8-8 1-8" fill="none" stroke="#fff" stroke-width="2.5"/></svg></div>
  <div class="feature-icon abs" style="left:562px"><svg width="36" height="36"><circle cx="13" cy="23" r="8" fill="#fff"/><path d="M17 19L31 5" stroke="#fff" stroke-width="3"/></svg></div>
  <div class="feature-icon abs" style="left:697px"><svg width="42" height="26"><rect x="1" y="1" width="40" height="24" fill="#fff"/><path d="M6 1v24M11 1v24M16 1v24M21 1v24M26 1v24M31 1v24M36 1v24" stroke="#d22" stroke-width="1"/><path d="M8.5 1v14M18.5 1v14M23.5 1v14M33.5 1v14" stroke="#222" stroke-width="3"/></svg></div>
  <p>Lorem ipsum dolor sit amet, consectetuer adipiscing elit, sed diam nonummy nibh euismod tincidunt ut laoreet dolore<br>magna aliquam erat volutpat. Ut wisi enim ad minim veniam, quis nostrud exerci tation ullamcorper</p>
</section>

<article class="info-card abs" style="left:132px">
  <div class="head"></div><div class="badge"><svg width="52" height="52"><path d="M17 36V18l16-4v18" fill="none" stroke="#111" stroke-width="3"/><circle cx="14" cy="36" r="4" fill="#111"/><circle cx="30" cy="32" r="4" fill="#111"/></svg></div>
  <div class="kicker">Music News &amp;</div><div class="title">EVENTS</div>
  <div class="date">23-Jun-2014</div>
  <div class="body">Nulla egestas mi non pulvinar sodales. Vesti bulum id luctus augue. Integer sem nisl, susc ipit sit amet cursus non, venenatis</div>
  <div class="go"><svg width="12" height="10"><path d="M0 3h6V0l6 5-6 5V7H0z" fill="#e81a12"/></svg></div>
</article>
<article class="info-card abs" style="left:358px">
  <div class="head"></div><div class="badge"><svg width="52" height="52"><circle cx="20" cy="32" r="8" fill="#111"/><path d="M24 28L38 14" stroke="#111" stroke-width="3"/></svg></div>
  <div class="kicker">Music Teachers</div><div class="title">AVAILABLE</div>
  <div class="teachers" role="img" aria-label="Small portraits of available teachers"><i></i><i></i><i></i><i></i><i></i></div>
  <div class="body">Nulla egestas mi non pulvinar sodales. Vesti bulum id luctus augue. Integer sem nisl, susc ipit sit amet cursus non, venenatis</div>
  <div class="go"><svg width="12" height="10"><path d="M0 3h6V0l6 5-6 5V7H0z" fill="#e81a12"/></svg></div>
</article>
<article class="info-card abs" style="left:583px">
  <div class="head"></div><div class="badge"><svg width="52" height="52"><rect x="21" y="8" width="10" height="18" rx="5" fill="#111"/><path d="M17 22a9 9 0 0 0 18 0M26 31v10" fill="none" stroke="#111" stroke-width="2.5"/></svg></div>
  <div class="kicker">Music Products</div><div class="title">HIGHLIGHTS</div>
  <div class="body" style="top:46px">Nulla egestas mi non pulvinar sodales. Vesti bulum id luctus augue. Integer sem nisl, susc ipit sit amet cursus non, venenatis Praesent aliquet mauris ante,</div>
  <div class="go"><svg width="12" height="10"><path d="M0 3h6V0l6 5-6 5V7H0z" fill="#e81a12"/></svg></div>
</article>

<div class="featured-bar abs">
  <h2>FEATURED PRODUCTS</h2>
  <div class="pager abs" style="left:603px"><svg width="12" height="10"><path d="M12 3H6V0L0 5l6 5V7h6z" fill="#888"/></svg></div>
  <div class="pager abs" style="left:627px"><svg width="12" height="10"><path d="M0 3h6V0l6 5-6 5V7H0z" fill="#888"/></svg></div>
</div>

<div class="product abs" style="left:130px">
  <div class="shot" role="img" aria-label="Photo of an alto sax"></div>
  <div class="stars">★★★☆☆</div><h3>Alto Sax</h3>
  <p>vitae adipiscing urna accumsan vitae.<br>Nunc varius nunc ut nisl</p><div class="price">$249.99</div>
  <div class="actions"><div class="add">🛒 Add to Cart</div><div class="mini"><svg width="11" height="9"><path d="M1 9V7M4 9V5M7 9V3M10 9V1" stroke="#2a2" stroke-width="1.5"/></svg></div><div class="mini" style="color:#2a2;font-size:11px">☆</div></div>
</div>
<div class="product abs" style="left:299px">
  <div class="shot" role="img" aria-label="Photo of a trombone"></div>
  <div class="stars">★★★☆☆</div><h3>Trombone</h3>
  <p>vitae adipiscing urna accumsan vitae.<br>Nunc varius nunc ut nisl</p><div class="price">$249.99</div>
  <div class="actions"><div class="add">🛒 Add to Cart</div><div class="mini"><svg width="11" height="9"><path d="M1 9V7M4 9V5M7 9V3M10 9V1" stroke="#2a2" stroke-width="1.5"/></svg></div><div class="mini" style="color:#2a2;font-size:11px">☆</div></div>
</div>
<div class="product abs" style="left:468px">
  <div class="shot" role="img" aria-label="Photo of a clarinet"></div>
  <div class="stars">★★★☆☆</div><h3>Clarinet</h3>
  <p>vitae adipiscing urna accumsan vitae.<br>Nunc varius nunc ut nisl</p><div class="price">$249.99</div>
  <div class="actions"><div class="add">🛒 Add to Cart</div><div class="mini"><svg width="11" height="9"><path d="M1 9V7M4 9V5M7 9V3M10 9V1" stroke="#2a2" stroke-width="1.5"/></svg></div><div class="mini" style="color:#2a2;font-size:11px">☆</div></div>
</div>
<div class="product abs" style="left:636px">
  <div class="shot" role="img" aria-label="Photo of a flute"></div>
  <div class="stars">★★★☆☆</div><h3>Flute</h3>
  <p>vitae adipiscing urna accumsan vitae.<br>Nunc varius nunc ut nisl</p><div class="price">$249.99</div>
  <div class="actions"><div class="add">🛒 Add to Cart</div><div class="mini"><svg width="11" height="9"><path d="M1 9V7M4 9V5M7 9V3M10 9V1" stroke="#2a2" stroke-width="1.5"/></svg></div><div class="mini" style="color:#2a2;font-size:11px">☆</div></div>
</div>

<footer class="site-footer abs"></footer>
<div class="footer-links abs"><span>HOME</span><span>ABOUT</span><span>FEATURES</span><span>BLOG</span><span>CONTACT</span></div>
<div class="contact-line abs" style="left:130px"><b><svg width="11" height="8"><rect x=".5" y=".5" width="10" height="7" fill="none" stroke="#222"/><path d="M.5 .5l5 4 5-4" fill="none" stroke="#222"/></svg></b>info@cresthornsupply.com</div>
<div class="contact-line abs" style="left:322px"><b><svg width="10" height="10"><path d="M2 1l2 2-1 2 2 2 2-1 2 2-2 2C4 9 1 6 0 3z" fill="#222"/></svg></b>408-555-0142</div>
<div class="copyright abs">Copyright© 2014 All Right Reserved <span>CRESTHORNSUPPLY.COM</span></div>
<div class="news-title abs">Sign up for our <span>Newsletter</span></div>
<div class="field abs" style="top:1077px">Name</div>
<div class="field abs" style="top:1108px">Email</div>
<div class="field subscribe abs" style="top:1140px">Subscribe</div>

</body>
</html>
```